Delegate visit agenda

We need a creative, yet simple and official design for an agenda to be handed out for delegates visiting our organization. The design needs to be creative, informative and visual when possible. Flat design is desired but other options are welcomed. The agenda should be 3 pages in lengths only. Page 1 should have the company logo with an event title (with the ability to add country flag) and the dates of the event. Pages 2 should include photos of receiving delegate (e.g. VIPs) and any other relevant people. Page 3 should include agenda entries with the following information: title of entry, date and time, location, relevant pictures (e.g. a hotel or flight). The generic style of an infographic.
Updates
Project Deadline Extended
Reason: Not enough submissions received.
No optimal design (i.e. creative and attractive) received.

Brief has been updated with samples.

Target Market(s)
Very high profile people (e.g. presidents, ministers, GM,...etc.)
Industry/Entity Type
Hotel
Colors
Designer to choose colors to be used in the design.
Look and feel
Each slider illustrates characteristics of the customer's brand and the style your logo design should communicate.

```html
<!DOCTYPE html>
<html lang="en">
<head>
<meta charset="utf-8">
<title>Programme</title>
<link rel="stylesheet" href="https://fonts.googleapis.com/css2?family=Roboto+Slab:wght@700;900&family=Tinos:wght@400;700&family=Open+Sans:ital,wght@0,400;0,700;1,400&display=swap">
<style>
:root{
  --paper:#faf7f0;
  --gold:#b8862b;
  --ink:#231f20;
  --white:#ffffff;
}
*{box-sizing:border-box;margin:0;padding:0}
html,body{width:1200px;height:849px;overflow:hidden;background:var(--paper)}
.canvas{position:relative;width:1200px;height:849px;background:var(--paper);color:var(--ink);font-family:"Tinos",Georgia,serif}
.route{position:absolute;left:0;top:0}
.title{position:absolute;left:67px;top:68px;font-family:"Roboto Slab",Georgia,serif;font-weight:900;font-size:32px;letter-spacing:.5px}
.entry h3{font-family:"Roboto Slab",Georgia,serif;font-weight:700;font-size:13px;line-height:16px}
.entry h4{font-weight:400;font-size:11px;line-height:15px;margin-bottom:3px}
.entry p{font-size:11px;line-height:13.3px;text-align:justify}
.note{position:absolute;width:266px}
.stop{position:absolute;border-radius:50%;background:var(--white);border:3px solid var(--gold);box-shadow:2px 3px 6px rgba(0,0,0,.28)}
.stop .entry{position:absolute}
.badge{position:absolute;width:54px;height:54px;margin:-27px 0 0 -27px;border-radius:50%;background:var(--ink);color:var(--white);text-align:center;font-family:"Open Sans",Arial,sans-serif}
.badge::after{content:"";position:absolute;left:22px;bottom:-7px;border-left:5px solid transparent;border-right:5px solid transparent;border-top:9px solid var(--ink)}
.badge .day{display:block;font-size:21px;font-weight:700;line-height:22px;margin-top:7px}
.badge .time{display:block;font-size:10px;font-style:italic;line-height:12px}
.marker{position:absolute;width:11px;height:11px;margin:-5.5px 0 0 -5.5px;border-radius:50%;background:var(--white);border:2.5px solid var(--ink)}
.legend{position:absolute;left:0;top:795px;width:1200px;height:34px}
.legend-item{position:absolute;top:0;display:flex;align-items:center;gap:5px;font-family:"Open Sans",Arial,sans-serif;font-size:11px}
.legend-item svg{fill:var(--ink)}
</style>
</head>
<body>
<main class="canvas">
  <svg class="route" width="1200" height="849" viewBox="0 0 1200 849" aria-hidden="true">
    <path d="M322 98 C360 104 390 112 420 116 L470 128 M560 158 C600 176 640 192 680 205 M790 265 C830 292 860 316 910 330 M960 385 C1000 420 1050 450 1090 520 C1140 600 1140 690 1090 730 C1040 760 960 760 907 752 C850 745 770 735 699 711 C620 690 560 650 490 625 C450 610 430 595 413 582 C370 555 330 530 307 512 C280 490 255 470 220 440" fill="none" stroke="var(--gold)" stroke-width="4.5" stroke-linecap="round" stroke-dasharray="0 11"/>
  </svg>

  <h1 class="title">PROGRAMME</h1>

  <section class="entry note" style="left:68px;top:117px">
    <h3>Lorem ipsum</h3><h4>LOREM IPSUM</h4>
    <p>Lorem ipsum dolor sit amet, error regione voluptua mea ei, ei ullum civibus efficiantur pri. Ei exerci reprimique has. Duo te dicant complectitur, pri ei nihil munere doctus. Vix id exerci verear, mea ea accusata petentium ullamcorper. Vel offendit percipit maluisset ea.</p>
  </section>
  <section class="entry note" style="left:357px;top:235px">
    <h3>Lorem ipsum</h3><h4>LOREM IPSUM</h4>
    <p>Lorem ipsum dolor sit amet, error regione voluptua mea ei, ei ullum civibus efficiantur pri. Ei exerci reprimique has. Duo te dicant complectitur, pri ei nihil munere doctus. Vix id exerci verear, mea ea accusata petentium ullamcorper. Vel offendit percipit maluisset ea.</p>
  </section>
  <section class="entry note" style="left:647px;top:358px">
    <h3>Lorem ipsum</h3><h4>LOREM IPSUM</h4>
    <p>Lorem ipsum dolor sit amet, error regione voluptua mea ei, ei ullum civibus efficiantur pri. Ei exerci reprimique has. Duo te dicant complectitur, pri ei nihil munere doctus. Vix id exerci verear, mea ea accusata petentium ullamcorper. Vel offendit percipit maluisset ea.</p>
  </section>

  <div class="stop" style="left:445px;top:25px;width:146px;height:146px">
    <div class="entry" style="left:25px;top:22px;width:100px"><h3>Lorem ipsum</h3><h4>LOREM IPSUM</h4><p>Lorem ipsum dolor sit amet, error regione voluptua mea ei, ei ullum</p></div>
  </div>
  <div class="stop" style="left:663px;top:68px;width:226px;height:226px">
    <div class="entry" style="left:32px;top:30px;width:158px"><h3>Lorem ipsum</h3><h4>LOREM IPSUM</h4><p>Lorem ipsum dolor sit amet, error regione voluptua mea ei, ei ullum civibus efficiantur pri. Ei exerci reprimique has. Duo te dicant complectitur, pri ei nihil munere doctus. Vix id</p></div>
  </div>
  <div class="stop" style="left:899px;top:216px;width:182px;height:178px">
    <div class="entry" style="left:27px;top:20px;width:138px"><h3>Lorem ipsum</h3><h4>LOREM IPSUM</h4><p>Lorem ipsum dolor sit amet, error regione voluptua mea ei, ei ullum civibus efficiantur pri. Ei exerci reprimique has. Duo te dicant complectitur, pri ei</p></div>
  </div>
  <div class="stop" style="left:901px;top:469px;width:179px;height:178px">
    <div class="entry" style="left:26px;top:31px;width:138px"><h3>Lorem ipsum</h3><h4>LOREM IPSUM</h4><p>Lorem ipsum dolor sit amet, error regione voluptua mea ei, ei ullum civibus efficiantur pri. Ei exerci reprimique has. Duo te dicant complectitur, pri ei</p></div>
  </div>
  <div class="stop" style="left:762px;top:599px;width:162px;height:148px">
    <div class="entry" style="left:20px;top:21px;width:104px"><h3>Lorem ipsum</h3><h4>LOREM IPSUM</h4><p>Lorem ipsum dolor sit amet, error regione voluptua mea ei, ei ullum civibus efficiantur</p></div>
  </div>
  <div class="stop" style="left:509px;top:507px;width:178px;height:178px">
    <div class="entry" style="left:32px;top:22px;width:138px"><h3>Lorem ipsum</h3><h4>LOREM IPSUM</h4><p>Lorem ipsum dolor sit amet, error regione voluptua mea ei, ei ullum civibus efficiantur pri. Ei exerci reprimique has. Duo te dicant complectitur, pri ei</p></div>
  </div>
  <div class="stop" style="left:321px;top:361px;width:178px;height:180px">
    <div class="entry" style="left:28px;top:27px;width:138px"><h3>Lorem ipsum</h3><h4>LOREM IPSUM</h4><p>Lorem ipsum dolor sit amet, error regione voluptua mea ei, ei ullum civibus efficiantur pri. Ei exerci reprimique has. Duo te dicant complectitur, pri ei</p></div>
  </div>
  <div class="stop" style="left:105px;top:307px;width:142px;height:142px">
    <div class="entry" style="left:8px;top:19px;width:100px"><h3>Lorem ipsum</h3><h4>LOREM IPSUM</h4><p>Lorem ipsum dolor sit amet, error regione voluptua mea ei, ei ullum</p></div>
  </div>
  <div class="stop" style="left:99px;top:519px;width:223px;height:223px">
    <div class="entry" style="left:11px;top:38px;width:176px"><h3>Lorem ipsum</h3><h4>LOREM IPSUM</h4><p>Lorem ipsum dolor sit amet, error regione voluptua mea ei, ei ullum civibus efficiantur pri. Ei exerci reprimique has. Duo te dicant complectitur, pri ei nihil munere doctus. Vix id exerci verear, mea ea accusata petentium ullamcorper. Vel offendit percipit maluisset ea.</p></div>
  </div>

  <span class="marker" style="left:408px;top:113px"></span>
  <span class="marker" style="left:624px;top:184px"></span>
  <span class="marker" style="left:862px;top:313px"></span>
  <span class="marker" style="left:1016px;top:439px"></span>
  <span class="marker" style="left:907px;top:752px"></span>
  <span class="marker" style="left:699px;top:711px"></span>
  <span class="marker" style="left:413px;top:582px"></span>
  <span class="marker" style="left:307px;top:512px"></span>
  <span class="marker" style="left:239px;top:460px"></span>

  <div class="badge" style="left:440px;top:74px"><span class="day">10</span><span class="time">5:30pm</span></div>
  <div class="badge" style="left:652px;top:148px"><span class="day">11</span><span class="time">10:00am</span></div>
  <div class="badge" style="left:892px;top:275px"><span class="day">11</span><span class="time">6:00pm</span></div>
  <div class="badge" style="left:978px;top:462px"><span class="day">12</span><span class="time">8:00am</span></div>
  <div class="badge" style="left:908px;top:703px"><span class="day">12</span><span class="time">12:00pm</span></div>
  <div class="badge" style="left:700px;top:662px"><span class="day">12</span><span class="time">7:00pm</span></div>
  <div class="badge" style="left:446px;top:546px"><span class="day">13</span><span class="time">9:00am</span></div>
  <div class="badge" style="left:283px;top:548px"><span class="day">13</span><span class="time">1:00pm</span></div>
  <div class="badge" style="left:241px;top:410px"><span class="day">13</span><span class="time">5:00pm</span></div>

  <footer class="legend">
    <div class="legend-item" style="left:78px"><svg width="20" height="30" viewBox="0 0 20 30"><path d="M10 0a9 9 0 0 0-9 9c0 7 9 20 9 20s9-13 9-20a9 9 0 0 0-9-9zm0 13a4 4 0 1 1 0-8 4 4 0 0 1 0 8z"/></svg>Lorem ipsum</div>
    <div class="legend-item" style="left:209px"><svg width="30" height="28" viewBox="0 0 30 28"><path d="M7 2h16l6 7-14 18L1 9z" fill="none" stroke="var(--ink)" stroke-width="2"/><path d="M1 9h28M11 2l-3 7 7 18 7-18-3-7M8 9l7-7 7 7" fill="none" stroke="var(--ink)" stroke-width="1.5"/></svg>Lorem ipsum</div>
    <div class="legend-item" style="left:345px"><svg width="30" height="30" viewBox="0 0 30 30"><circle cx="15" cy="15" r="15"/><path d="M15 7c3 3 3 8 0 12-3-4-3-9 0-12zM7 12c4 0 7 3 8 7-4 0-7-3-8-7zm16 0c-4 0-7 3-8 7 4 0 7-3 8-7zM8 21h14" fill="var(--white)" stroke="var(--white)" stroke-width="1"/></svg>Lorem ipsum</div>
    <div class="legend-item" style="left:483px"><svg width="30" height="30" viewBox="0 0 30 30"><circle cx="15" cy="16" r="11" fill="none" stroke="var(--ink)" stroke-width="3"/><path d="M15 10v7l4 3" stroke="var(--ink)" stroke-width="2" fill="none"/><path d="M2 7l6-5 2 3-5 4zm26 0l-6-5-2 3 5 4zM7 27l2-3m14 3-2-3" stroke="var(--ink)" stroke-width="2"/></svg>Lorem ipsum</div>
    <div class="legend-item" style="left:620px"><svg width="30" height="30" viewBox="0 0 30 30"><circle cx="15" cy="15" r="13" fill="none" stroke="var(--ink)" stroke-width="3"/><path d="M21 9l-4 8-8 4 4-8z"/></svg>Lorem ipsum</div>
    <div class="legend-item" style="left:748px"><svg width="40" height="30" viewBox="0 0 40 30"><rect x="1" y="2" width="24" height="15" rx="2" fill="none" stroke="var(--ink)" stroke-width="2"/><path d="M6 17l-2 5 6-5" fill="none" stroke="var(--ink)" stroke-width="2"/><rect x="13" y="10" width="24" height="14" rx="2" fill="var(--paper)" stroke="var(--ink)" stroke-width="2"/><path d="M31 24l3 5-7-5" fill="var(--paper)" stroke="var(--ink)" stroke-width="2"/></svg>Lorem ipsum</div>
    <div class="legend-item" style="left:893px"><svg width="32" height="30" viewBox="0 0 32 30"><circle cx="11" cy="11" r="7" fill="none" stroke="var(--ink)" stroke-width="5" stroke-dasharray="3 2.5"/><circle cx="11" cy="11" r="5"/><circle cx="11" cy="11" r="2" fill="var(--paper)"/><circle cx="24" cy="21" r="5" fill="none" stroke="var(--ink)" stroke-width="4" stroke-dasharray="2.5 2"/><circle cx="24" cy="21" r="3.5"/><circle cx="24" cy="21" r="1.5" fill="var(--paper)"/></svg>Lorem ipsum</div>
    <div class="legend-item" style="left:1025px"><svg width="40" height="30" viewBox="0 0 40 30"><path d="M2 20l8-1 6-16h4l-3 14 12-2 4-5h3l-2 7 3 2-17 4-8 5h-4l4-6-8 1z"/></svg>Lorem ipsum</div>
  </footer>
</main>
</body>
</html>
```